PillPeak website blog. Simple medical advice given in clear yes or no answers that save people money

I am developing a new web page that provides medical care cost savings at the consumers' fingertips. I need a web page that is clean, concise, and attractive for me to put my valuable medical information on. The information I provide is simple to obtain, yet very valuable to the consumer, and answered in a yes or no format. For example, A person may wonder if they need an antibiotic for cold like symptoms. Seeing a doctor for an antibiotic is very expensive. But with simple and clear advice at their fingertips, they can confidently avoid having to pay $200 or more to see a doctor and get an antibiotic. This is kind of like consumer reports for medical services.

Target Market(s)

People who are savvy shoppers and want to save money on healthcare. Likely younger ages between 21 and 60, who are mobile, readily use iphones, and want strong evidence based research to guide their decisions.

Industry/Entity Type

Coding

Number of Pages Required

Colors

Requirements
Must have
• A template on the "Question" and "Answer" page that can be edited many times that can be edited many times. The Confidence rating scale would need to be edited as well. The "Date Researched" the "PillPeak Pilluminate" and "References" all need to be able to be edited. This website must be very clear and simple to understand. A medical question is posed with a yes or no answer, then answered and given a confidence rating, we then tell them how much money they saved by going to our website.
Nice to have
• We want this to be slightly fun, vibrant, warm and inviting. This will be sometime later converted into an app format. Quirky, some humor to keep it interesting.
Should not have
• No sterile looking medical images. Not boring.

```html
<!DOCTYPE html>
<html lang="en">
<head>
<meta charset="utf-8">
<title>PillPeak — Clear. Valuable. Health. Advice.</title>
<link href="https://fonts.googleapis.com/css2?family=Cinzel:wght@400&family=Mulish:wght@400;700;800&display=swap" rel="stylesheet">
<style>
  :root{
    --bg-light:#ececec;
    --brand-red:#e0001f;
    --brand-blue:#1a63b8;
    --action-green:#16983a;
    --footer-dark:#221e1f;
    --text-dark:#444;
    --white:#fff;
  }
  *{box-sizing:border-box;margin:0;padding:0}
  html,body{width:1167px;height:1200px;overflow:hidden}
  body{background:var(--bg-light);font-family:"Mulish",sans-serif;color:var(--text-dark);position:relative}

  .site-header{height:143px;position:relative}
  .brand{position:absolute;left:108px;top:48px;display:flex;align-items:center;gap:8px}
  .brand-dot{width:22px;height:22px;border-radius:50%;background:var(--brand-blue)}
  .brand-name{font-weight:800;font-size:32px;color:var(--brand-red)}
  .tagline{position:absolute;left:298px;top:48px;font-family:"Cinzel",serif;font-size:33px;color:var(--brand-red);letter-spacing:.5px;white-space:nowrap}

  .main-nav{height:56px;background:var(--brand-blue);display:flex;align-items:center;padding-left:117px}
  .main-nav a{color:var(--white);text-decoration:none;font-size:15.5px;margin-right:46px}
  .main-nav a:last-child{margin-right:0}

  .search{position:absolute;left:108px;top:228px;width:950px;height:44px;display:flex}
  .search-input{flex:1;border:1px solid #8a8a8a;border-right:none;font-size:13px;color:#666;padding-left:15px;display:flex;align-items:center}
  .search-button{width:121px;background:var(--action-green);color:var(--white);font-weight:700;font-size:15px;display:flex;align-items:center;justify-content:center}

  .hero{position:absolute;left:0;top:313px;width:1167px;height:520px}
  .hero-photo{position:absolute;inset:0;background:linear-gradient(110deg,#4a6a8c 0%,#2f6f95 35%,#1a8aa5 55%,#2a6790 80%,#4a6d90 100%)}
  .info-menu{position:absolute;left:108px;top:89px;width:297px;list-style:none}
  .info-menu li{height:50px;margin-bottom:2px;background:var(--brand-red);color:var(--white);font-weight:800;font-size:17px;display:flex;align-items:center;justify-content:space-between;padding:0 27px}
  .info-menu li:last-child{height:56px}
  .info-menu svg{width:8px;height:10px}
  .hero-copy{position:absolute;right:109px;top:132px;text-align:right;color:var(--white)}
  .hero-copy h1{font-size:37px;font-weight:800;line-height:46px}
  .hero-copy .free{font-size:90px;font-weight:800;line-height:1;margin-top:12px}
  .slider-dots{position:absolute;left:561px;top:449px;display:flex;gap:4px}
  .slider-dots span{width:13px;height:13px;border-radius:50%;background:var(--white)}
  .slider-dots span.active{background:transparent;border:1.5px solid var(--white)}

  .site-footer{position:absolute;left:0;top:833px;width:1167px;height:367px;background:var(--footer-dark);color:var(--white)}
  .footer-brand{position:absolute;left:108px;top:150px;display:flex;align-items:center;gap:8px}
  .footer-brand .brand-dot{background:var(--white)}
  .footer-brand .brand-name{color:var(--white);font-size:36px}
  .disclaimer{position:absolute;left:376px;top:80px;width:270px}
  .disclaimer h2,.signup h2{font-weight:400;font-size:20px;margin-bottom:12px}
  .disclaimer p{font-size:10px;line-height:20px}
  .signup{position:absolute;left:710px;top:80px;width:348px}
  .signup-form{height:43px;background:var(--white);display:flex;padding:2px}
  .signup-input{flex:1;color:#666;font-size:13px;display:flex;align-items:center;padding-left:14px}
  .signup-button{width:117px;background:var(--brand-red);font-weight:800;font-size:13.5px;display:flex;align-items:center;justify-content:center}
  .ask-box{margin-top:16px;height:97px;background:var(--action-green);display:flex;align-items:center;padding:0 20px 0 19px;justify-content:space-between}
  .ask-box svg{width:78px;height:56px}
  .ask-text{text-align:right}
  .ask-text strong{display:block;font-size:22px;font-weight:800}
  .ask-text span{font-size:16px}
  .footer-rule{position:absolute;left:108px;top:297px;width:950px;height:1px;background:#3a3536}
  .copyright{position:absolute;left:0;width:1167px;top:324px;text-align:center;font-size:13px}
</style>
</head>
<body>
  <header class="site-header">
    <div class="brand"><span class="brand-dot"></span><span class="brand-name">PillPeak</span></div>
    <p class="tagline">Clear. Valuable. Health. Advice. Right Now.</p>
  </header>

  <nav class="main-nav">
    <a href="#">Prev/Screening</a><a href="#">Women's Health</a><a href="#">Men's Health</a><a href="#">Meds</a><a href="#">Surgery</a><a href="#">Imaging</a><a href="#">Peds</a><a href="#">Contranergies</a>
  </nav>

  <div class="search">
    <div class="search-input">Search entire here</div>
    <div class="search-button">Search</div>
  </div>

  <section class="hero">
    <div class="hero-photo" role="img" aria-label="Close-up of gloved hands handling medical tubing"></div>
    <ul class="info-menu">
      <li>Who are We?<svg viewBox="0 0 8 10"><path d="M0 0L8 5L0 10Z" fill="#fff"/></svg></li>
      <li>How it Works<svg viewBox="0 0 8 10"><path d="M0 0L8 5L0 10Z" fill="#fff"/></svg></li>
      <li>How we Know<svg viewBox="0 0 8 10"><path d="M0 0L8 5L0 10Z" fill="#fff"/></svg></li>
      <li>Evidence based Research<svg viewBox="0 0 8 10"><path d="M0 0L8 5L0 10Z" fill="#fff"/></svg></li>
      <li>Dr. Whitmore<svg viewBox="0 0 8 10"><path d="M0 0L8 5L0 10Z" fill="#fff"/></svg></li>
      <li>Who we are not<svg viewBox="0 0 8 10"><path d="M0 0L8 5L0 10Z" fill="#fff"/></svg></li>
      <li>Are we Based?<svg viewBox="0 0 8 10"><path d="M0 0L8 5L0 10Z" fill="#fff"/></svg></li>
    </ul>
    <div class="hero-copy">
      <h1>Don't Spend another time on your<br>health before checking us out!</h1>
      <p class="free">It's Free!</p>
    </div>
    <div class="slider-dots"><span class="active"></span><span></span><span></span></div>
  </section>

  <footer class="site-footer">
    <div class="footer-brand"><span class="brand-dot"></span><span class="brand-name">PillPeak</span></div>
    <div class="disclaimer">
      <h2>Disclaimer</h2>
      <p>At vero eos et accusamus et iusto odio dignissimos ducimus qui blanditiis praesentium voluptatum deleniti atque corrupti quos dolores</p>
    </div>
    <div class="signup">
      <h2>Become a PillPeak Today!</h2>
      <div class="signup-form"><div class="signup-input">Enter email</div><div class="signup-button">SUBMIT NOW</div></div>
      <div class="ask-box">
        <svg viewBox="0 0 78 56" fill="none" stroke="#fff" stroke-width="3">
          <path d="M44 18c14 0 30 6 30 18 0 6-3 10-6 12l2 7-9-4c-5 2-12 2-17 0"/>
          <path d="M29 4C14 4 3 13 3 25c0 6 3 11 7 14l-3 10 11-6c3 1 7 2 11 2 15 0 26-9 26-20S44 4 29 4Z"/>
          <path d="M22 19c0-5 4-8 8-8s8 3 8 7-4 6-7 8v5" stroke-linecap="round"/>
          <circle cx="31" cy="37" r="1.5" fill="#fff"/>
        </svg>
        <div class="ask-text"><strong>Ask a question here!</strong><span>If it is worthy well Post it!</span></div>
      </div>
    </div>
    <div class="footer-rule"></div>
    <p class="copyright">Copyrights © 2018 PillPeak. All rights reserved.</p>
  </footer>
</body>
</html>
```